Business Card Design

I need a bussiness card that have some picture of a van and lorry.
Updates

Hello I could ask you to print business cards and message to the home address?

Industry/Entity Type

Business

Contact Information for Business Card

K&M Transport LTD
truck and vans fridge
drivers recruitment
k.m-transport@corvellmail.com
tel nr 07823415069

```html
<!DOCTYPE html>
<html lang="en">
<head>
<meta charset="utf-8">
<title>K&amp;M Transport LTD — Business Card</title>
<link href="https://fonts.googleapis.com/css2?family=Questrial&family=Roboto:ital,wght@1,700&display=swap" rel="stylesheet">
<style>
  :root {
    --backdrop: #a3a39f;
    --card: #000000;
    --headline: #ffffff;
    --contact: #f2c200;
    --ribbon-top: #a3191c;
    --ribbon-bottom: #7e1013;
    --rule: #4a0b0c;
    --sky-top: #8f9aa3;
    --sky-bottom: #3e454c;
    --city-top: #b9cfe2;
    --city-bottom: #4c5560;
  }
  * { margin: 0; padding: 0; box-sizing: border-box; }
  html, body {
    width: 1200px;
    height: 743px;
    overflow: hidden;
    background: var(--backdrop);
  }
  .card {
    position: absolute;
    left: 30px;
    top: 35px;
    width: 1140px;
    height: 665px;
    background: var(--card);
    overflow: hidden;
  }
  .photo { position: absolute; }
  .photo--truck {
    left: 0; top: 89px; width: 313px; height: 194px;
    background: linear-gradient(170deg, var(--sky-top) 0%, #6d767e 45%, var(--sky-bottom) 100%);
  }
  .photo--vans {
    left: 313px; top: 284px; width: 270px; height: 194px;
    background: linear-gradient(180deg, var(--city-top) 0%, #8ea6bb 50%, var(--city-bottom) 100%);
  }
  .headline {
    position: absolute;
    right: 66px;
    top: 110px;
    text-align: right;
    color: var(--headline);
    font-family: "Questrial", sans-serif;
    font-size: 36px;
    line-height: 54px;
    font-weight: 400;
  }
  .contact {
    position: absolute;
    top: 535px;
    left: 12px;
    display: flex;
    align-items: center;
    color: var(--contact);
    font-family: "Questrial", sans-serif;
    font-size: 30px;
  }
  .contact__icon { width: 34px; height: 34px; margin-right: 10px; flex: none; }
  .contact__item { display: flex; align-items: center; }
  .contact__item + .contact__item { margin-left: 20px; }
  .ribbon {
    position: absolute;
    left: 786px;
    top: 519px;
    width: 354px;
    height: 52px;
  }
  .ribbon__label {
    position: absolute;
    left: 58px;
    top: 0;
    height: 52px;
    line-height: 52px;
    color: #ffffff;
    font-family: "Roboto", sans-serif;
    font-style: italic;
    font-weight: 700;
    font-size: 28px;
  }
  .rule {
    position: absolute;
    left: 0;
    top: 615px;
    width: 100%;
    height: 2px;
    background: var(--rule);
  }
</style>
</head>
<body>
  <main class="card">
    <div class="photo photo--truck" role="img" aria-label="Photo of a refrigerated lorry driving on a mountain road"></div>
    <div class="photo photo--vans" role="img" aria-label="Photo of two delivery vans driving on a city road"></div>

    <h1 class="headline">
      K&amp;M Transport LTD truck<br>
      and<br>
      vans fridge drivers recruitment
    </h1>

    <div class="contact">
      <span class="contact__item">
        <svg class="contact__icon" viewBox="0 0 34 34" aria-hidden="true">
          <circle cx="17" cy="17" r="15" fill="none" stroke="currentColor" stroke-width="2.4"/>
          <circle cx="17" cy="17" r="4.5" fill="none" stroke="currentColor" stroke-width="2.4"/>
          <path d="M21.5 13 v6 a2.5 2.5 0 0 0 5 0 v-2 a9.5 9.5 0 1 0 -3.5 7.4" fill="none" stroke="currentColor" stroke-width="2.4" stroke-linecap="round"/>
        </svg>
        k.m-transport@corvellmail.com
      </span>
      <span class="contact__item">
        <svg class="contact__icon" viewBox="0 0 34 34" aria-hidden="true">
          <circle cx="17" cy="17" r="15" fill="none" stroke="currentColor" stroke-width="2.4"/>
          <path d="M11.5 9.5 l3 -0.5 l2 4.5 l-2 1.5 c1 2.5 2.5 4 5 5 l1.5 -2 l4.5 2 l-0.5 3 c-7 1 -14 -6 -13.5 -13.5 z" fill="currentColor"/>
        </svg>
        07823415069
      </span>
    </div>

    <div class="ribbon">
      <svg width="354" height="52" viewBox="0 0 354 52" aria-hidden="true">
        <defs>
          <linearGradient id="ribbonFill" x1="0" y1="0" x2="0" y2="1">
            <stop offset="0" stop-color="var(--ribbon-top)"/>
            <stop offset="0.55" stop-color="var(--ribbon-top)"/>
            <stop offset="1" stop-color="var(--ribbon-bottom)"/>
          </linearGradient>
        </defs>
        <polygon points="0,0 354,0 354,52 28,52" fill="url(#ribbonFill)"/>
      </svg>
      <span class="ribbon__label">Express Delivery</span>
    </div>

    <div class="rule"></div>
  </main>
</body>
</html>
```